Single-sided business card for restaurant velmora with new logo made on this site

Business card options with new logo including restaurant name, address, phone number and website. This business card is single-sided only and will be presented at the hostess desk for clients to take. I would like to see options based on a cream card background, a white card background, a yellow card background and a burgundy colored background. It needs to be elegant and traditional.

Target Market(s)

local and international crowd

Industry/Entity Type

restaurant

Contact Information for Business Card

address, website and phone number

Font styles to use
Serif

Colors
EE7325
F08F49
F5BC92
FAE3D3
FDF4ED

Requirements
Must have
• new logo, address, phone number, website
Should not have
• more than three colors

```html
<!DOCTYPE html>
<html lang="es">
<head>
<meta charset="utf-8">
<title>Restaurant Velmora – Business Cards</title>
<link rel="stylesheet" href="https://fonts.googleapis.com/css2?family=PT+Sans:wght@400&display=swap">
<style>
  :root {
    --backdrop: #8e8e8e;
    --burgundy: #7a1315;
    --saffron: #fcb03c;
    --cream: #fdf9ee;
    --cocoa: #3d1316;
    --ink-dark: #3b1214;
    --ink-light: #fdf4ed;
    --font-text: "PT Sans", "Helvetica Neue", Arial, sans-serif;
  }
  * { box-sizing: border-box; margin: 0; padding: 0; }
  html, body { width: 1021px; height: 1200px; overflow: hidden; background: var(--backdrop); }
  body { position: relative; font-family: var(--font-text); }

  .card {
    position: absolute; left: 91px; width: 840px; height: 480px; overflow: hidden;
  }
  .card--burgundy { top: 80px; background: var(--saffron); --wave: var(--burgundy); --ink: var(--ink-light); --icon: var(--saffron); }
  .card--saffron { top: 624px; background: var(--cream); --wave: var(--saffron); --ink: var(--ink-dark); --icon: var(--ink-light); }

  .card__wave { position: absolute; inset: 0; width: 840px; height: 480px; }
  .card__wave path { fill: var(--wave); }

  .brand-mark {
    position: absolute; left: 86px; top: 82px; width: 213px; height: 312px;
    background: var(--cocoa); display: flex; align-items: center; justify-content: center;
  }
  .brand-mark__name {
    color: var(--ink-light); font-size: 36px; letter-spacing: 6px; font-weight: 400;
  }

  .details { position: absolute; left: 0; top: 0; width: 100%; height: 100%; color: var(--ink); }
  .details__title { position: absolute; left: 406px; top: 108px; font-size: 36px; font-weight: 400; white-space: nowrap; }
  .details__line { position: absolute; left: 473px; font-size: 21px; line-height: 33px; white-space: nowrap; }
  .details__line--phone { top: 186px; }
  .details__line--address { top: 231px; }
  .details__line--web { top: 341px; }

  .icon { position: absolute; left: 407px; width: 24px; height: 24px; fill: none; stroke: var(--icon); stroke-width: 1.6; stroke-linecap: round; stroke-linejoin: round; }
  .icon--phone { top: 190px; }
  .icon--pin { top: 235px; }
  .icon--pointer { top: 346px; }
</style>
</head>
<body>

<section class="card card--burgundy" aria-label="Business card, burgundy version">
  <svg class="card__wave" viewBox="0 0 840 480" aria-hidden="true"><path d="M242 0 C180 120 168 330 266 480 L840 480 L840 0 Z"/></svg>
  <div class="brand-mark"><span class="brand-mark__name">VELMORA</span></div>
  <div class="details">
    <h1 class="details__title">Restaurant Velmora</h1>
    <svg class="icon icon--phone" viewBox="0 0 24 24" aria-hidden="true"><path d="M5 3h3l2 5-2 1.5a11 11 0 0 0 6.5 6.5L16 14l5 2v3a2 2 0 0 1-2 2A16 16 0 0 1 3 5a2 2 0 0 1 2-2z"/><path d="M15 3a6 6 0 0 1 6 6M15 6.5a2.5 2.5 0 0 1 2.5 2.5"/></svg>
    <p class="details__line details__line--phone">Reservaciones 958-412-3370</p>
    <svg class="icon icon--pin" viewBox="0 0 24 24" aria-hidden="true"><path d="M12 22s7-7 7-12.5A7 7 0 0 0 5 9.5C5 15 12 22 12 22z"/><circle cx="12" cy="9.5" r="2.5"/></svg>
    <p class="details__line details__line--address">Jacarandá 418<br>Bahías de Huatulco,<br>Oaxaca CP 70989</p>
    <svg class="icon icon--pointer" viewBox="0 0 24 24" aria-hidden="true"><path d="M6 3l12 10-5.5 1L16 20l-2.5 1.2-3.3-6.2L6 19z"/></svg>
    <p class="details__line details__line--web">www.velmora.com.mx</p>
  </div>
</section>

<section class="card card--saffron" aria-label="Business card, saffron version">
  <svg class="card__wave" viewBox="0 0 840 480" aria-hidden="true"><path d="M242 0 C180 120 168 330 266 480 L840 480 L840 0 Z"/></svg>
  <div class="brand-mark"><span class="brand-mark__name">VELMORA</span></div>
  <div class="details">
    <h1 class="details__title">Restaurant Velmora</h1>
    <svg class="icon icon--phone" viewBox="0 0 24 24" aria-hidden="true"><path d="M5 3h3l2 5-2 1.5a11 11 0 0 0 6.5 6.5L16 14l5 2v3a2 2 0 0 1-2 2A16 16 0 0 1 3 5a2 2 0 0 1 2-2z"/><path d="M15 3a6 6 0 0 1 6 6M15 6.5a2.5 2.5 0 0 1 2.5 2.5"/></svg>
    <p class="details__line details__line--phone">Reservaciones 958-412-3370</p>
    <svg class="icon icon--pin" viewBox="0 0 24 24" aria-hidden="true"><path d="M12 22s7-7 7-12.5A7 7 0 0 0 5 9.5C5 15 12 22 12 22z"/><circle cx="12" cy="9.5" r="2.5"/></svg>
    <p class="details__line details__line--address">Jacarandá 418<br>Bahías de Huatulco,<br>Oaxaca CP 70989</p>
    <svg class="icon icon--pointer" viewBox="0 0 24 24" aria-hidden="true"><path d="M6 3l12 10-5.5 1L16 20l-2.5 1.2-3.3-6.2L6 19z"/></svg>
    <p class="details__line details__line--web">www.velmora.com.mx</p>
  </div>
</section>

</body>
</html>
```